Larkspur Cosmetics Website needs a professional upgrade

I need a new design for an online cosmetics store that looks professional and clean but also has a natural look and feel to it.

The women in the top bar (Image attached) needs to be included and she is on all of our advertising banners/ stands though I would like to come away from the black.

Design Needs:
- 1 x Home Page
- 1 x Products Page

I have plenty more website coming along so hopefully can find someone who I can rely on for a quick turnover :)

Happy designing !

Industry/Entity Type

Store

Number of Pages Required

2 page

Font styles to use
Sans Serif

Requirements
Must have
• - Natural Clean look
Should not have
• - The current black and green colours

```html
<!DOCTYPE html>
<html lang="en">
<head>
<meta charset="utf-8">
<title>Larkspur Cosmetics — Natural Skincare</title>
<link href="https://fonts.googleapis.com/css2?family=Montserrat:wght@400;500;600;700&display=swap" rel="stylesheet">
<style>
:root{
  --orange:#ff6a33;
  --yellow:#fbc30e;
  --ink:#333333;
  --muted:#9a9a9a;
  --line:#e6e6e6;
  --paper:#ffffff;
  --soft:#f7f7f7;
  --footer:#f9f9f9;
}
*{box-sizing:border-box;margin:0;padding:0}
html,body{width:1200px;height:2473px;overflow:hidden;background:var(--paper)}
body{position:relative;font-family:"Montserrat",Arial,sans-serif;color:var(--ink)}
.abs{position:absolute}
a{color:inherit;text-decoration:none}

/* header */
.header{left:0;top:0;width:1200px;height:145px;background:var(--paper)}
.util{display:flex;align-items:center;gap:8px;font-size:11px;color:#555}
.util svg{flex:none}
.util.phone{left:219px;top:66px;font-size:14px;font-weight:600;color:#444}
.util.ship{left:376px;top:67px}
.util.cartlinks{left:709px;top:66px}
.util.cartlinks .sep{color:#aaa;margin:0 4px}
.brand{left:520px;top:14px;width:160px;text-align:center}
.brand-mark{width:62px;height:62px;border-radius:50%;background:var(--orange);margin:0 auto 8px}
.brand-name{font-size:15px;font-weight:600;letter-spacing:1.5px;color:#3a3a3a;line-height:1.25}

/* nav */
.nav{left:0;top:145px;width:1200px;height:66px;background:var(--orange)}
.categories{left:190px;top:0;width:136px;height:66px;background:var(--yellow);color:#fff;font-size:13px;font-weight:700;display:flex;align-items:center;justify-content:center;gap:8px}
.menu{left:340px;top:0;height:66px;display:flex;align-items:center;gap:0}
.menu a{color:#fff;font-size:11px;font-weight:600;padding:0 12px;line-height:66px;position:relative}
.menu a.active::after{content:"";position:absolute;left:10px;right:10px;bottom:16px;height:3px;background:#fff}

/* hero */
.hero{left:0;top:211px;width:1200px;height:516px;background:linear-gradient(90deg,#f4f5f7 0%,#f8f8f9 100%)}
.hero-photo{left:0;top:0;width:560px;height:516px;background:radial-gradient(ellipse at 45% 40%,#e8c3a8 0%,#d9ae92 35%,#e9eef5 75%,#eef1f6 100%)}
.hero-kicker{left:559px;top:232px;font-size:30px;font-weight:700;color:var(--yellow)}
.hero-title{left:559px;top:268px;font-size:43px;font-weight:700;color:var(--orange);letter-spacing:-.3px}
.btn-outline{left:565px;top:348px;width:165px;height:50px;border:2px solid var(--yellow);border-radius:5px;color:var(--orange);font-size:13px;font-weight:700;display:flex;align-items:center;justify-content:center}
.dots{left:1152px;top:372px;display:flex;flex-direction:column;gap:12px}
.dots span{width:9px;height:9px;border-radius:50%;background:#777}
.dots span.on{background:#c7a43f}

/* concern cards */
.concern{top:801px;width:252px;height:229px;background:#eee;box-shadow:0 12px 14px -8px rgba(0,0,0,.25)}
.concern .photo{position:absolute;left:0;top:0;width:252px;height:155px}
.concern .label{position:absolute;left:0;top:155px;width:252px;height:74px;background:var(--orange);color:#fff;font-size:20px;font-weight:700;line-height:1.1;display:flex;align-items:center;padding:0 50px 0 19px}
.concern .go{position:absolute;right:17px;top:50%;margin-top:-12px}

/* featured */
.section-title{left:0;top:1150px;width:1200px;text-align:center;font-size:33px;font-weight:700;color:var(--yellow)}
.divider{top:1236px;width:1px;height:352px;background:var(--line)}
.product{top:1236px;width:250px;text-align:center}
.product .pack{width:130px;height:190px;margin:0 auto}
.product .name{margin-top:23px;font-size:12px;font-weight:700;color:var(--orange)}
.product .kind{margin-top:8px;font-size:12px;color:var(--muted)}
.product .price{margin-top:6px;font-size:26px;font-weight:500;color:#444}
.btn-cart{display:inline-flex;margin-top:10px;width:116px;height:36px;background:var(--orange);color:#fff;font-size:10px;font-weight:700;align-items:center;justify-content:center}
.pager{top:1653px;display:flex;gap:12px;left:575px}

/* newsletter */
.signup{left:0;top:1727px;width:1200px;height:452px;background:linear-gradient(90deg,#d9b9a2 0%,#e4d3c0 40%,#e8e1d0 70%,#ebe6d6 100%)}
.signup-photo{left:0;top:0;width:640px;height:452px;background:radial-gradient(ellipse at 30% 50%,#dcb49a 0%,#d6ad93 40%,rgba(232,224,208,0) 80%)}
.signup-title{left:635px;top:168px;font-size:27px;font-weight:500;color:var(--orange);line-height:1.35}
.email{left:631px;top:257px;width:384px;height:51px;background:#fff;border:1px solid #999;font-size:11px;color:#bbb;padding:0 20px;display:flex;align-items:center}
.btn-subscribe{left:631px;top:325px;width:145px;height:43px;background:var(--yellow);color:#fff;font-size:12px;font-weight:700;display:flex;align-items:center;justify-content:center}

/* footer */
.footer{left:0;top:2179px;width:1200px;height:240px;background:var(--footer)}
.footer-brand{left:214px;top:48px;width:124px;text-align:center}
.footer-brand .brand-mark{width:58px;height:58px;margin-bottom:10px}
.footer-brand .brand-name{font-size:14px}
.fcol{top:43px}
.fcol h4{font-size:12px;font-weight:700;color:var(--orange);margin-bottom:18px}
.fcol li{list-style:none;font-size:10px;color:#444;line-height:27px}
.fcol.nohead{top:82px}
.bottombar{left:0;top:2419px;width:1200px;height:54px;border-top:1px solid var(--line);background:var(--paper);font-size:10px;font-weight:600;color:#333}
.bottombar .copy{position:absolute;left:201px;top:21px}
.bottombar .legal{position:absolute;left:862px;top:21px}
</style>
</head>
<body>

<header class="abs header">
  <div class="abs util phone">
    <svg width="16" height="16" viewBox="0 0 24 24"><path fill="#ff6a33" d="M6.6 10.8a15.1 15.1 0 006.6 6.6l2.2-2.2a1 1 0 011-.25 11.4 11.4 0 003.6.57 1 1 0 011 1V20a1 1 0 01-1 1A17 17 0 013 4a1 1 0 011-1h3.5a1 1 0 011 1c0 1.25.2 2.45.57 3.57a1 1 0 01-.25 1z"/></svg>
    (02) 5550 1234
  </div>
  <div class="abs util ship">
    <svg width="18" height="14" viewBox="0 0 24 18"><path fill="#ff6a33" d="M1 2h13v10H1zM14 6h5l4 4v2h-9z"/><circle cx="6" cy="14" r="2.5" fill="#ff6a33"/><circle cx="18" cy="14" r="2.5" fill="#ff6a33"/></svg>
    $8 Shipping Aus Under 7 kg
  </div>
  <div class="abs brand">
    <div class="brand-mark"></div>
    <div class="brand-name">LARKSPUR<br>COSMETICS</div>
  </div>
  <div class="abs util cartlinks">
    <svg width="14" height="16" viewBox="0 0 14 16"><path fill="#ff6a33" d="M1 4h12l-1 12H2z"/><path d="M4 5V3a3 3 0 016 0v2" stroke="#ff6a33" fill="none" stroke-width="1.5"/></svg>
    <span>Your Shopping Bag</span><span class="sep">|</span>
    <svg width="18" height="16" viewBox="0 0 24 20"><path fill="#ff6a33" d="M0 1h4l3 11h13l3-8H7"/><circle cx="9" cy="17" r="2" fill="#ff6a33"/><circle cx="19" cy="17" r="2" fill="#ff6a33"/></svg>
    <span>View Cart</span><span class="sep">|</span>
    <svg width="18" height="18" viewBox="0 0 18 18"><circle cx="9" cy="9" r="9" fill="#ff6a33"/><path d="M5 9.5l3 3 5-6" stroke="#fff" stroke-width="2" fill="none"/></svg>
    <span>Checkout</span>
  </div>
</header>

<nav class="abs nav">
  <div class="abs categories">Categories
    <svg width="10" height="6" viewBox="0 0 10 6"><path d="M1 1l4 4 4-4" stroke="#ff6a33" stroke-width="1.6" fill="none"/></svg>
  </div>
  <div class="abs menu">
    <a class="active">Home</a><a>About Us</a><a>Products</a><a>About Aloe</a><a>Treatments</a><a>Media</a><a>Success Stories</a><a>Stockists</a><a>Contact Us</a>
  </div>
</nav>

<section class="abs hero">
  <div class="abs hero-photo" role="img" aria-label="Portrait of the brand model with hand resting on her cheek"></div>
  <div class="abs hero-kicker">Your Natural</div>
  <div class="abs hero-title">Skincare Specialists</div>
  <a class="abs btn-outline">SHOP NOW</a>
  <div class="abs dots"><span class="on"></span><span></span><span></span><span></span></div>
</section>

<section>
  <div class="abs concern" style="left:201px">
    <div class="photo" role="img" aria-label="Woman applying cream to her arm" style="background:linear-gradient(135deg,#f3e6dc,#d9b49b)"></div>
    <div class="label">Eczema &amp;<br>Psoriasis
      <svg class="go" width="24" height="24" viewBox="0 0 24 24"><circle cx="12" cy="12" r="12" fill="#fff"/><path d="M10 7l5 5-5 5" stroke="#ff6a33" stroke-width="2.4" fill="none"/></svg></div>
  </div>
  <div class="abs concern" style="left:475px">
    <div class="photo" role="img" aria-label="Young woman with towel checking her skin" style="background:linear-gradient(135deg,#f1e0d4,#ddb7a1)"></div>
    <div class="label">Acne
      <svg class="go" width="24" height="24" viewBox="0 0 24 24"><circle cx="12" cy="12" r="12" fill="#fff"/><path d="M10 7l5 5-5 5" stroke="#ff6a33" stroke-width="2.4" fill="none"/></svg></div>
  </div>
  <div class="abs concern" style="left:747px">
    <div class="photo" role="img" aria-label="Man holding his stomach in discomfort" style="background:linear-gradient(135deg,#c9c9c9,#e3b2a4)"></div>
    <div class="label">Irritable<br>Bowel Syndrome
      <svg class="go" width="24" height="24" viewBox="0 0 24 24"><circle cx="12" cy="12" r="12" fill="#fff"/><path d="M10 7l5 5-5 5" stroke="#ff6a33" stroke-width="2.4" fill="none"/></svg></div>
  </div>
</section>

<section>
  <h2 class="abs section-title">Featured Products</h2>
  <div class="abs divider" style="left:481px"></div>
  <div class="abs divider" style="left:733px"></div>
  <div class="abs product" style="left:203px">
    <div class="pack" role="img" aria-label="Treatment cream tube and green box" style="background:linear-gradient(90deg,#f2f2f2 0%,#e9eccf 50%,#7d8a2a 100%)"></div>
    <div class="name">Skin Ease®</div>
    <div class="kind">Treatment Cream</div>
    <div class="price">$35.00</div>
    <a class="btn-cart">ADD TO CART</a>
  </div>
  <div class="abs product" style="left:475px">
    <div class="pack" role="img" aria-label="Serum bottle and gold box" style="background:linear-gradient(90deg,#e8e8e8 0%,#3a3a3a 50%,#8a7a3c 100%)"></div>
    <div class="name">Revitalising Seru</div>
    <div class="kind">Treatment Cream</div>
    <div class="price">$35.00</div>
    <a class="btn-cart">ADD TO CART</a>
  </div>
  <div class="abs product" style="left:747px">
    <div class="pack" role="img" aria-label="Lotion tube and purple box" style="background:linear-gradient(90deg,#f2f2f2 0%,#e6d9ea 50%,#6d2a7a 100%)"></div>
    <div class="name">Hydrating Hand &amp; Body Lotion</div>
    <div class="kind">Treatment Cream</div>
    <div class="price">$35.00</div>
    <a class="btn-cart">ADD TO CART</a>
  </div>
  <div class="abs pager">
    <svg width="25" height="25" viewBox="0 0 25 25"><circle cx="12.5" cy="12.5" r="12.5" fill="#9a9a9a"/><path d="M14.5 7.5l-5 5 5 5" stroke="#fff" stroke-width="2.4" fill="none"/></svg>
    <svg width="25" height="25" viewBox="0 0 25 25"><circle cx="12.5" cy="12.5" r="12.5" fill="#9a9a9a"/><path d="M10.5 7.5l5 5-5 5" stroke="#fff" stroke-width="2.4" fill="none"/></svg>
  </div>
</section>

<section class="abs signup">
  <div class="abs signup-photo" role="img" aria-label="Close-up of the brand model's face"></div>
  <div class="abs signup-title">Sign up for Specials and<br>Health &amp; Beauty Tips</div>
  <div class="abs email">Enter Your E-mail Address</div>
  <a class="abs btn-subscribe">SUBSCRIBE NOW</a>
</section>

<footer class="abs footer">
  <div class="abs footer-brand">
    <div class="brand-mark"></div>
    <div class="brand-name">LARKSPUR<br>COSMETICS</div>
  </div>
  <div class="abs fcol" style="left:384px">
    <h4>Menu Links</h4>
    <ul><li>Home</li><li>About Us</li><li>Products</li><li>About Aloe</li><li>Treatments</li></ul>
  </div>
  <div class="abs fcol nohead" style="left:519px">
    <ul><li>Media</li><li>Success Stories</li><li>Stockists</li><li>Contact Us</li></ul>
  </div>
  <div class="abs fcol" style="left:676px">
    <h4>Other Links</h4>
    <ul><li>Shipping</li><li>Terms &amp; Conditions</li><li>Privacy Promotions</li><li>Site map</li></ul>
  </div>
  <div class="abs fcol" style="left:862px">
    <h4>Quick Links</h4>
    <ul><li>My account</li><li>Log in / Register</li><li>Orders</li></ul>
  </div>
</footer>

<div class="abs bottombar">
  <span class="copy">Copyright © 2016 Larkspur Cosmetics® Pty Ltd | All Rights Reserved.</span>
  <span class="legal">Term Of Use | Privacy Policy</span>
</div>

</body>
</html>
```